Motel Sign - Front

(21/03/12 - I've edited the brief and removing the words "garden view" its not fitting in the designs I'm getting and just want the word motel to be the focus. I have a template/vision of what I want - see the whiteboard sketch of what I'm looking for uploaded today. Definitely open to creatively, new designs and different ideas but the whiteboard design I've done should be a guideline. Keep it fresh/green/white. use the sample photos of green as inspiration. Thanks)
We are a motel set in the mountain country of Victoria - Australia. The front of the motel needs a fresh look. We recently removed a large amount of the garden to expose a brick courtyard fence which the front of the courtyard faces out to the main road. Within the courtyard fence there is a wooden frame and paneling.
We want to have a new sign created to slot into the wooden frame. (see photo) its the white component.
Its a very large and unusual shape and I want to keep it simple but need to fill the in the best way possible.
The space is 940mm high and 4940mm width.
The message of the sign is simple the word "MOTEL". I want people to be able to drive past and glance in and see we are a motel straight away. So the main purpose of the sign is to say "MOTEL".
I am open to colour use to match the space and have impact. I thought a background colour should be 'off white'. I'm open to the colours used to match your design as long as it matches the brief. Maybe a garden green for the emblem.
IN BRIEF:
1) the word "MOTEL"
2) Border/Background that ties in the garden.
The design should be centred, clean and simple, doesn't have to fill the whole space as long as its balanced and centred.
I like cursive and garden like designs for this one - as long its the word MOTEL still has impact. (OPEN TO NEW IDEAS)
I am also open to different ideas and suggestions if you feel you have a better way to take advantage of this space.
The sign will be 7-8 metres from the road itself.
NOTE: the photos show the space and the painted white in the space where the sign will go. The garden in front of this space will be completely cleared.
Motel

```html
<!DOCTYPE html>
<html lang="en">
<head>
<meta charset="utf-8">
<title>Motel Sign – Front</title>
<link rel="stylesheet" href="https://fonts.googleapis.com/css2?family=Cinzel:wght@900&display=swap">
<style>
  :root {
    --page-bg: #ffffff;
    --leaf-light: #d4e68a;
    --leaf-mid: #a9d15a;
    --leaf-deep: #5fae3a;
    --fern: #3f9a32;
    --ink-green: #0b4a22;
    --outline: #ffffff;
  }
  html, body {
    margin: 0;
    padding: 0;
    width: 1200px;
    height: 524px;
    overflow: hidden;
    background: var(--page-bg);
  }
  .canvas {
    position: relative;
    width: 1200px;
    height: 524px;
  }
  .sign-panel {
    position: absolute;
    left: 72px;
    top: 162px;
    width: 1095px;
    height: 207px;
    overflow: hidden;
    background:
      radial-gradient(ellipse 40% 70% at 30% 40%, #e3ee93 0%, rgba(227,238,147,0) 70%),
      linear-gradient(90deg, var(--leaf-mid) 0%, var(--leaf-light) 30%, #bfdc6e 60%, var(--leaf-mid) 85%, #8fc64b 100%);
  }
  .garden-ornament {
    position: absolute;
    top: 0;
    height: 207px;
  }
  .garden-ornament--left {
    left: 0;
    width: 200px;
    background: radial-gradient(ellipse 80% 90% at 20% 85%, rgba(63,154,50,0.75) 0%, rgba(95,174,58,0.35) 50%, rgba(169,209,90,0) 100%);
  }
  .garden-ornament--right {
    right: 0;
    width: 260px;
    background: radial-gradient(ellipse 85% 95% at 80% 75%, rgba(63,154,50,0.8) 0%, rgba(95,174,58,0.4) 50%, rgba(169,209,90,0) 100%);
  }
  .sign-word {
    position: absolute;
    left: 0;
    top: 0;
    width: 1200px;
    height: 524px;
  }
  .sign-word text {
    font-family: "Cinzel", "Times New Roman", serif;
    font-weight: 900;
    font-size: 232px;
    fill: var(--ink-green);
    stroke: var(--outline);
    stroke-width: 9px;
    stroke-linejoin: round;
    paint-order: stroke fill;
  }
</style>
</head>
<body>
  <div class="canvas">
    <div class="sign-panel">
      <div class="garden-ornament garden-ornament--left" role="img" aria-label="White vine tendrils, fern leaves and green swirl ornaments"></div>
      <div class="garden-ornament garden-ornament--right" role="img" aria-label="White vine tendrils, fern leaves and green swirl ornaments"></div>
    </div>
    <svg class="sign-word" viewBox="0 0 1200 524" width="1200" height="524">
      <text x="262" y="342" textLength="700" lengthAdjust="spacingAndGlyphs">MOTEL</text>
    </svg>
  </div>
</body>
</html>
```